Dorwin's Coating & Renewal Letterhead Design We want to revamp out old traditional letterhead with the new logo designs that are attached. We are working on getting all our company items from vehicles, business, cards, t-shirts, letterhead to match. This should include company colors, fonts, and flow of items that we have attached below.

Industry/Entity Type

Construction Company

Font styles to use
Sans Serif
Other font styles liked:
• Bold with outline

Colors
ec1f27
ffffff

Requirements
Must have
• Company Name: Dorwin's Coating & Renewal
• Address: 4728 SW 81st Ter Halverd cove fl 39417
• Office Number: (555) 413-2986
• Email: Dorwinrenewal@mailbrook.example
• License Number: KRT8046392
Nice to have
• Company Colors: red, white, black, and grey

```html
<!DOCTYPE html>
<html lang="en">
<head>
<meta charset="utf-8">
<title>Dorwin's Coating &amp; Renewal — Letterhead</title>
<link href="https://fonts.googleapis.com/css2?family=Arimo:wght@400;700&display=swap" rel="stylesheet">
<style>
  :root {
    --brand-red: #ec1f27;
    --ink-black: #1c1c1c;
    --body-grey: #6d6d6d;
    --rule-grey: #2a2a2a;
    --paper: #ffffff;
    --backdrop: #dfe1e2;
  }
  * { box-sizing: border-box; margin: 0; padding: 0; }
  html, body {
    width: 1200px; height: 784px; overflow: hidden;
    background: var(--backdrop);
    font-family: "Arimo", Arial, sans-serif;
  }
  .letterhead {
    position: absolute; left: 338px; top: 22px;
    width: 524px; height: 740px;
    background: var(--paper);
    box-shadow: 0 2px 10px rgba(0,0,0,0.12);
    overflow: hidden;
  }
  .edge-stripes { position: absolute; left: 0; top: 0; width: 22px; height: 740px; }
  .brand {
    position: absolute; right: 34px; top: 36px;
    display: flex; align-items: center; gap: 7px;
  }
  .brand-mark { width: 14px; height: 14px; background: var(--brand-red); }
  .brand-name {
    font-weight: 700; font-size: 17px; letter-spacing: 0.5px;
    color: var(--brand-red); text-transform: uppercase; line-height: 1.1;
    text-align: right; width: 150px;
  }
  .header-rule { position: absolute; left: 300px; top: 104px; width: 196px; height: 10px; }
  .contact {
    position: absolute; right: 30px; top: 116px; width: 240px;
    font-size: 7px; line-height: 1.55; color: var(--body-grey); text-align: right;
  }
  .contact .address { color: var(--brand-red); font-weight: 700; }
  .contact svg { width: 7px; height: 7px; vertical-align: -1px; margin: 0 2px 0 4px; }
  .letter-body {
    position: absolute; left: 78px; top: 168px; width: 340px;
    font-size: 8.6px; line-height: 1.55; color: var(--body-grey);
  }
  .letter-body p { margin-bottom: 12px; text-indent: 14px; }
  .signature-area {
    width: 150px; height: 48px; margin-top: 14px;
    background: linear-gradient(90deg, #f1f1f1, #f7f7f7);
  }
</style>
</head>
<body>
  <main class="letterhead">
    <svg class="edge-stripes" viewBox="0 0 22 740" aria-hidden="true">
      <rect x="0" y="0" width="6" height="740" fill="var(--ink-black)"/>
      <rect x="11" y="0" width="8" height="300" fill="var(--ink-black)"/>
      <rect x="11" y="306" width="8" height="230" fill="var(--brand-red)"/>
      <rect x="11" y="542" width="8" height="90" fill="var(--ink-black)"/>
      <rect x="11" y="638" width="8" height="102" fill="var(--brand-red)"/>
    </svg>

    <header class="brand">
      <div class="brand-name">Dorwin's Coating &amp; Renewal</div>
      <span class="brand-mark"></span>
    </header>

    <svg class="header-rule" viewBox="0 0 196 10" aria-hidden="true">
      <line x1="0" y1="5" x2="190" y2="5" stroke="var(--rule-grey)" stroke-width="1"/>
      <rect x="188" y="1" width="8" height="8" fill="var(--brand-red)"/>
    </svg>

    <address class="contact" style="font-style:normal">
      <div class="address">
        <svg viewBox="0 0 10 10"><circle cx="5" cy="5" r="5" fill="var(--brand-red)"/><path d="M5 2.2a1.8 1.8 0 0 1 1.8 1.8C6.8 5.4 5 7.8 5 7.8S3.2 5.4 3.2 4A1.8 1.8 0 0 1 5 2.2z" fill="#fff"/></svg>4728 SW 81st Ter Halverd cove fl 39417
      </div>
      <div>
        <svg viewBox="0 0 10 10"><circle cx="5" cy="5" r="5" fill="var(--brand-red)"/><path d="M3.2 2.6l1 1-.5.8a4 4 0 0 0 1.9 1.9l.8-.5 1 1-.6.8C4.9 7.6 2.4 5.1 2.4 3.2z" fill="#fff"/></svg>(555) 413-2986
        <svg viewBox="0 0 10 10"><circle cx="5" cy="5" r="5" fill="var(--brand-red)"/><path d="M3 5.2l1.4 1.4L7 3.8" stroke="#fff" stroke-width="1" fill="none"/></svg>License: KRT8046392
      </div>
      <div>
        <svg viewBox="0 0 10 10"><circle cx="5" cy="5" r="5" fill="var(--brand-red)"/><rect x="2.6" y="3.4" width="4.8" height="3.4" fill="none" stroke="#fff" stroke-width=".8"/><path d="M2.6 3.4L5 5.3l2.4-1.9" stroke="#fff" stroke-width=".8" fill="none"/></svg>Dorwinrenewal@mailbrook.example
        <svg viewBox="0 0 10 10"><circle cx="5" cy="5" r="5" fill="var(--brand-red)"/><circle cx="5" cy="5" r="2.4" fill="none" stroke="#fff" stroke-width=".8"/><line x1="2.6" y1="5" x2="7.4" y2="5" stroke="#fff" stroke-width=".6"/></svg>www.dorwinrenewal.example
      </div>
    </address>

    <section class="letter-body">
      <p>Lorem Ipsum is simply dummy text of the printing and typesetting industry. Lorem Ipsum has been the industry's standard dummy text ever since the 1500s, when an unknown printer took a galley of type and scrambled it to make a type specimen book. It has survived not only five centuries, but also the leap into electronic typesetting, remaining essentially unchanged. It was popularised in the 1960s with the release of Typeleaf sheets containing Lorem Ipsum passages, and more recently with desktop publishing software like Quillset Layout including versions of Lorem Ipsum.</p>
      <p>It is a long established fact that a reader will be distracted by the readable content of a page when looking at its layout. The point of using Lorem Ipsum is that it has a more-or-less normal distribution of letters, as opposed to using 'Content here, content here', making it look like readable English. Many desktop publishing packages and web page editors now use Lorem Ipsum as their default model text, and a search for 'lorem ipsum' will uncover many web sites still in their infancy. Various versions have evolved over the years, sometimes by accident, sometimes on purpose (injected humour and the like).</p>
      <p>Contrary to popular belief, Lorem Ipsum is not simply random text. It has roots in a piece of classical Latin literature from 45 BC, making it over 2000 years old. Edmund Carrow, a Latin professor at Wexmoor College in Virginia, looked up one of the more obscure Latin words, consectetur, from a Lorem Ipsum passage, and going through the cites of the word in classical literature, discovered the undoubtable source. Lorem Ipsum comes from sections 1.10.32 and 1.10.33 of "de Finibus Bonorum et Malorum" structures, to generate Lorem Ipsum which looks reasonable. The generated Lorem Ipsum is therefore always free from repetition, injected humour, or non-characteristic words etc.</p>
      <div class="signature-area" role="img" aria-label="Space for the handwritten signature"></div>
    </section>
  </main>
</body>
</html>
```